Flight school sign for building, banner, and bilboard

This sign is primarily for use on the side of our flight school building to draw attention for current and future flight school students. We offer airplane and helicopter flight training, ground school training and seminars, airplane and helicopter rentals, multi-engine training, and more. I would like a professional but exciting sign that can be used across a multitude of signage options such as banners, banner ads, billboard, and other mediums so that our sign is consistent and recognizable.

Contact Information for Business Card

The business card should match our company sign somewhat but not exactly. We want good and exciting imagery or wording and energizing/exciting colors.

```html
<!DOCTYPE html>
<html lang="en">
<head>
<meta charset="utf-8">
<title>Corvane Aviation – Flight School Banner</title>
<link rel="stylesheet" href="https://fonts.googleapis.com/css2?family=Fira+Sans+Condensed:wght@500;600;700&family=Fira+Sans+Extra+Condensed:wght@600;700&display=swap">
<style>
  :root {
    --navy: #1a2750;
    --red: #ee1c25;
    --white: #ffffff;
    --page: #ececec;
    --sky-top: #5fb2ea;
    --sky-low: #cfe0ee;
    --cabin: #6d7176;
  }
  * { margin: 0; padding: 0; box-sizing: border-box; }
  html, body { width: 862px; height: 1200px; overflow: hidden; background: var(--page); }
  .canvas { position: relative; width: 862px; height: 1200px; }
  .banner {
    position: absolute; left: 86px; top: 428px; width: 689px; height: 344px;
    background: var(--white); overflow: hidden;
    box-shadow: 0 6px 10px rgba(0,0,0,.35);
    font-family: "Fira Sans Condensed", sans-serif;
  }
  .banner-shapes { position: absolute; inset: 0; }
  .brand { position: absolute; left: 37px; top: 76px; width: 240px; text-align: center; }
  .brand-name {
    font-family: "Fira Sans Condensed", sans-serif; font-weight: 500;
    font-size: 21px; line-height: 22px; letter-spacing: 1.5px;
    color: var(--navy); text-transform: uppercase;
  }
  .brand-tagline {
    font-weight: 600; font-size: 5.5px; letter-spacing: 1px; color: var(--red);
    text-transform: uppercase; margin-top: 1px;
  }
  .offer-title {
    position: absolute; left: 43px; top: 148px; width: 288px;
    display: flex; align-items: center; gap: 10px;
    font-family: "Fira Sans Extra Condensed", sans-serif; font-weight: 700;
    font-size: 25px; line-height: 30px; color: var(--white);
  }
  .offer-title::before, .offer-title::after { content: ""; flex: 1; height: 1px; background: var(--white); }
  .service { position: absolute; display: flex; align-items: center; gap: 8px; }
  .service-icon {
    width: 23px; height: 23px; border-radius: 50%; background: var(--red);
    border: 1.5px solid var(--white); flex: none;
  }
  .service-text {
    font-family: "Fira Sans Extra Condensed", sans-serif; font-weight: 600;
    font-size: 15px; line-height: 18px; color: var(--white);
  }
  .s1 { left: 20px; top: 188px; }
  .s2 { left: 197px; top: 188px; }
  .s3 { left: 20px; top: 246px; }
  .s4 { left: 197px; top: 246px; }
  .phone-pill {
    position: absolute; left: 20px; top: 306px; width: 159px; height: 29px;
    background: var(--red); border-radius: 15px;
    display: flex; align-items: center; gap: 8px; padding-left: 6px;
    font-family: "Fira Sans Extra Condensed", sans-serif; font-weight: 700;
    font-size: 18px; color: var(--white);
  }
  .contact-icon {
    width: 19px; height: 19px; border-radius: 50%; background: var(--white);
    display: flex; align-items: center; justify-content: center; flex: none;
  }
  .web {
    position: absolute; left: 196px; top: 307px;
    display: flex; align-items: center; gap: 7px;
    font-family: "Fira Sans Condensed", sans-serif; font-weight: 700;
    font-size: 20px; color: var(--navy);
  }
  .web .contact-icon { width: 22px; height: 22px; border: 1.5px solid var(--navy); }
  .web-domain { color: var(--red); }
</style>
</head>
<body>
<main class="canvas">
  <section class="banner">
    <svg class="banner-shapes" width="689" height="344" viewBox="0 0 689 344">
      <rect class="navy-body" x="0" y="85" width="689" height="259" fill="var(--navy)"/>
      <path class="header-panel" d="M0 0 H360 V84 Q175 158 0 100 Z" fill="var(--white)"/>
      <path class="header-band" d="M0 98 Q175 156 350 82 L350 96 Q175 176 0 115 Z" fill="var(--red)"/>
      <path class="footer-panel" d="M0 296 H446 Q500 320 525 344 H0 Z" fill="var(--white)"/>
      <path class="red-swoosh" d="M326 0 C340 200 470 344 606 344 C650 330 685 260 689 187 V140 C675 240 625 303 560 303 C445 303 362 160 345 0 Z" fill="var(--red)"/>
      <defs>
        <linearGradient id="cockpit-tone" x1="0" y1="0" x2="1" y2="1">
          <stop offset="0" stop-color="var(--sky-top)"/>
          <stop offset=".55" stop-color="var(--sky-low)"/>
          <stop offset="1" stop-color="var(--cabin)"/>
        </linearGradient>
      </defs>
      <path class="photo-frame" d="M340 0 C360 150 450 297 560 297 C640 297 689 220 689 140 V0 Z"
            fill="url(#cockpit-tone)" stroke="var(--white)" stroke-width="4"
            role="img" aria-label="Photo of a smiling pilot at the controls in a helicopter cockpit with blue sky beyond"/>
    </svg>

    <div class="brand">
      <div class="brand-name">Corvane Aviation</div>
      <div class="brand-tagline">Bold start today, open skies tomorrow</div>
    </div>

    <h2 class="offer-title">WE OFFER</h2>

    <div class="service s1"><span class="service-icon"></span><p class="service-text">Airplane and helicopter<br>flight training</p></div>
    <div class="service s2"><span class="service-icon"></span><p class="service-text">Ground school training<br>and seminars</p></div>
    <div class="service s3"><span class="service-icon"></span><p class="service-text">Airplane and<br>helicopter rentals</p></div>
    <div class="service s4"><span class="service-icon"></span><p class="service-text">Multi-engine training,<br>and more.</p></div>

    <div class="phone-pill">
      <span class="contact-icon">
        <svg width="11" height="11" viewBox="0 0 24 24"><path d="M6.6 10.8a15 15 0 0 0 6.6 6.6l2.2-2.2a1 1 0 0 1 1-.25 11.4 11.4 0 0 0 3.6.6 1 1 0 0 1 1 1V20a1 1 0 0 1-1 1A17 17 0 0 1 3 4a1 1 0 0 1 1-1h3.5a1 1 0 0 1 1 1c0 1.25.2 2.45.6 3.6a1 1 0 0 1-.25 1Z" fill="var(--navy)"/></svg>
      </span>
      (205) 555 0188
    </div>

    <div class="web">
      <span class="contact-icon">
        <svg width="13" height="13" viewBox="0 0 24 24" fill="none" stroke="var(--red)" stroke-width="2"><circle cx="12" cy="12" r="10"/><path d="M2 12h20M12 2c3 3 3 17 0 20M12 2c-3 3-3 17 0 20"/></svg>
      </span>
      <span>www.<span class="web-domain">corvaneaviation</span>.com</span>
    </div>
  </section>
</main>
</body>
</html>
```